Redesign current business card for food company

i would like to redesign my business card. our company is food company, our product range from chips, juices, milk and etc (mostly dried food stuff).
I want o keep same logo but , the rest is open to new design.
you can check at our website about our company www.orvelpantry.com

Target Market(s)

most of food company

Industry/Entity Type

Business

Contact Information for Business Card

I want to keep more to blue color...

Colors
3176b5
abd036

Requirements
Must have
• our old logo
Nice to have
• we do not mind to have nice material on bus card in order to accomplish nice design. for example: using spot uv, embossed and etc.

```html
<!DOCTYPE html>
<html lang="en">
<head>
<meta charset="utf-8">
<title>Orvel Business Card</title>
<link rel="stylesheet" href="https://fonts.googleapis.com/css2?family=Montserrat:wght@400;500;700&display=swap">
<style>
  :root {
    --bg: #eceef2;
    --card-white: #ffffff;
    --brand-violet: #5d63c4;
    --deep-blue: #2f33a3;
    --accent-teal: #2fb7d6;
    --accent-blue: #3176b5;
    --text-white: #ffffff;
    --text-dim: #e4e6fb;
    --edge-shadow: rgba(30, 34, 80, 0.18);
  }
  * { box-sizing: border-box; margin: 0; padding: 0; }
  html, body {
    width: 1200px; height: 913px; overflow: hidden;
    background: var(--bg);
    font-family: "Montserrat", Arial, sans-serif;
  }
  .canvas {
    position: relative; width: 1200px; height: 913px;
    display: flex; align-items: center; justify-content: center; gap: 60px;
  }
  .card {
    position: relative; width: 520px; height: 297px;
    border-radius: 14px; overflow: hidden;
    background: var(--card-white);
    box-shadow: 0 10px 28px var(--edge-shadow);
  }
  .card-art { position: absolute; inset: 0; width: 100%; height: 100%; }

  /* Front: contact side */
  .front-name {
    position: absolute; left: 36px; top: 126px;
    font-size: 40px; font-weight: 700; color: var(--accent-blue);
    letter-spacing: 3px; text-transform: uppercase;
  }
  .contact {
    position: absolute; right: 26px; top: 26px;
    text-align: right; color: var(--text-white);
  }
  .contact-name { font-size: 16px; font-weight: 700; letter-spacing: 0.2px; }
  .contact-title { font-size: 11px; color: var(--accent-teal); margin-top: 2px; font-weight: 500; }
  .contact-address { font-size: 11px; line-height: 1.45; margin-top: 16px; color: var(--text-dim); }
  .contact-lines { list-style: none; margin-top: 14px; font-size: 11.5px; line-height: 1.55; }
  .contact-lines li { display: flex; justify-content: flex-end; align-items: center; gap: 7px; }
  .contact-lines svg { width: 10px; height: 10px; flex: none; }

  /* Back: brand side */
  .back-name {
    position: absolute; left: 0; right: 0; top: 92px; text-align: center;
    font-size: 64px; font-weight: 700; color: var(--brand-violet);
    letter-spacing: 6px; text-transform: uppercase;
  }
  .back-url {
    position: absolute; left: 0; right: 0; top: 222px; text-align: center;
    font-size: 15px; font-weight: 500; color: var(--deep-blue); letter-spacing: 0.6px;
  }
  .back-edge {
    position: absolute; left: 0; right: 0; bottom: 0; height: 4px; background: var(--accent-teal);
  }
</style>
</head>
<body>
<main class="canvas">

  <section class="card card-front">
    <svg class="card-art" viewBox="0 0 520 297" preserveAspectRatio="none" aria-hidden="true">
      <defs>
        <linearGradient id="panelGradient" x1="0" y1="0" x2="0.3" y2="1">
          <stop offset="0" stop-color="#7a7fd0"/>
          <stop offset="0.55" stop-color="#4a4fbb"/>
          <stop offset="1" stop-color="#2f33a3"/>
        </linearGradient>
      </defs>
      <rect width="520" height="297" fill="url(#panelGradient)"/>
      <path d="M182 0 C300 60 330 200 306 297" fill="none" stroke="#ffffff" stroke-width="3"/>
      <path d="M172 0 C288 60 318 200 294 297" fill="none" stroke="#2fb7d6" stroke-width="3"/>
      <path d="M160 0 C276 60 306 200 282 297" fill="none" stroke="#3176b5" stroke-width="3"/>
      <path d="M0 0 H148 C264 60 294 200 270 297 H0 Z" fill="#ffffff"/>
    </svg>

    <p class="front-name">Orvel</p>

    <div class="contact">
      <p class="contact-name">Daniel Wirasmara</p>
      <p class="contact-title">President</p>
      <p class="contact-address">Orvel Enterprises Corp.<br>2480 Elmview Ave.<br>Ridgeford CA 90412</p>
      <ul class="contact-lines">
        <li>555 210 4418
          <svg viewBox="0 0 10 10"><path d="M2 1 L4 1 L4.6 3 L3.4 4 C4 5.4 4.8 6.2 6 6.6 L7 5.4 L9 6 L9 8 C5 8.6 1.4 5 2 1 Z" fill="#2fb7d6"/></svg>
        </li>
        <li>555 210 4427
          <svg viewBox="0 0 10 10"><rect x="1" y="2" width="8" height="5" rx="1" fill="#2fb7d6"/><rect x="3" y="7" width="4" height="2" fill="#2fb7d6"/></svg>
        </li>
        <li>555 372 9013
          <svg viewBox="0 0 10 10"><rect x="2.5" y="0.5" width="5" height="9" rx="1" fill="none" stroke="#2fb7d6" stroke-width="1.2"/></svg>
        </li>
        <li>daniel@orvelpantry.com
          <svg viewBox="0 0 10 10"><rect x="0.8" y="2" width="8.4" height="6" fill="none" stroke="#2fb7d6" stroke-width="1.1"/><path d="M1 2.4 L5 5.4 L9 2.4" fill="none" stroke="#2fb7d6" stroke-width="1.1"/></svg>
        </li>
        <li>www.orvelpantry.com
          <svg viewBox="0 0 10 10"><circle cx="5" cy="5" r="4.2" fill="none" stroke="#2fb7d6" stroke-width="1.1"/><path d="M0.8 5 H9.2 M5 0.8 C2.6 3 2.6 7 5 9.2 M5 0.8 C7.4 3 7.4 7 5 9.2" fill="none" stroke="#2fb7d6" stroke-width="0.9"/></svg>
        </li>
      </ul>
    </div>
  </section>

  <section class="card card-back">
    <p class="back-name">Orvel</p>
    <p class="back-url">www.orvelpantry.com</p>
    <div class="back-edge"></div>
  </section>

</main>
</body>
</html>
```